Managed IT services business card design

We haven't needed a business card since the founding of the business in 2005. All our clients have been coming through word of mouth. And lately more and more existing clients are requesting for our business cards to pass on to their contacts in recommending us.
So we needing a business card design. We use various innovative solutions and methodologies to provide IT services to small businesses in managing their IT systems. Our role is the same as an in-house, full-time IT Manager for our clients, but outsourced. So we take care of all our clients' IT needs, just as an IT Manager would be expected to perform.
We have a holding website, which we're happy to leave for now. If we can use the same logo would be great - www.lumadesk.com.au
Preferred colours are shades of are white, grey and black.
We pride our business with the following traits: proactive, good service, prompt response, trustworthy.
Target Market(s)
Small businesses of any industry
Industry/Entity Type
Business

```html
<!DOCTYPE html>
<html lang="en">
<head>
<meta charset="utf-8">
<title>lumadesk business card</title>
<link rel="stylesheet" href="https://fonts.googleapis.com/css2?family=Montserrat:wght@400;500&display=swap">
<style>
  :root {
    --stage: #e4e5e6;
    --card-white: #ffffff;
    --card-grey: #5c5f63;
    --ink: #1d1d1f;
    --ink-soft: #55585c;
    --on-grey: #f4f4f4;
    --shadow: rgba(0, 0, 0, 0.18);
  }
  * { box-sizing: border-box; margin: 0; padding: 0; }
  html, body {
    width: 1200px;
    height: 680px;
    overflow: hidden;
    background: var(--stage);
    font-family: "Montserrat", Arial, sans-serif;
  }
  .stage {
    position: relative;
    width: 1200px;
    height: 680px;
    display: flex;
    align-items: center;
    justify-content: center;
    gap: 60px;
  }
  .card {
    position: relative;
    width: 500px;
    height: 286px;
    box-shadow: 0 6px 18px var(--shadow);
    overflow: hidden;
  }

  /* Front */
  .card--front { background: var(--card-white); color: var(--ink); }
  .front__tab {
    position: absolute;
    top: 0;
    right: 0;
    width: 40px;
    height: 176px;
    background: var(--card-grey);
    border-top-left-radius: 20px;
    border-bottom-left-radius: 20px;
    display: flex;
    justify-content: center;
    padding-top: 16px;
  }
  .front__tab-url {
    writing-mode: vertical-rl;
    white-space: nowrap;
    font-size: 9.5px;
    letter-spacing: 2.2px;
    color: var(--on-grey);
  }
  .front__brand {
    position: absolute;
    left: 44px;
    top: 74px;
    display: flex;
    align-items: center;
    gap: 14px;
    font-size: 34px;
    font-weight: 400;
    letter-spacing: 9px;
    color: var(--ink);
  }
  .front__mark { width: 10px; height: 10px; background: var(--ink); }
  .front__person { position: absolute; left: 44px; top: 140px; }
  .front__name { font-size: 16px; font-weight: 500; }
  .front__role { font-size: 12px; color: var(--ink-soft); margin-top: 1px; }
  .front__contacts {
    position: absolute;
    left: 44px;
    top: 200px;
    list-style: none;
    font-size: 13px;
    line-height: 19px;
  }
  .front__contacts li { display: flex; align-items: center; gap: 8px; }
  .front__contacts svg { width: 13px; height: 13px; fill: var(--ink-soft); }
  .front__address {
    position: absolute;
    right: 56px;
    top: 184px;
    text-align: right;
    font-size: 12.5px;
    line-height: 17px;
    font-style: normal;
  }

  /* Back */
  .card--back { background: var(--card-grey); color: var(--on-grey); }
  .back__lockup {
    position: absolute;
    right: 46px;
    top: 104px;
    text-align: right;
  }
  .back__brand {
    display: flex;
    align-items: center;
    justify-content: flex-end;
    gap: 14px;
    font-size: 40px;
    letter-spacing: 10px;
    font-weight: 400;
  }
  .back__mark { width: 12px; height: 12px; background: var(--on-grey); }
  .back__url {
    margin-top: 8px;
    font-size: 12px;
    letter-spacing: 5px;
  }
</style>
</head>
<body>
<main class="stage">
  <section class="card card--front" aria-label="Business card front">
    <div class="front__tab">
      <span class="front__tab-url">www.lumadesk.com.au</span>
    </div>
    <h1 class="front__brand">lumadesk<span class="front__mark" aria-hidden="true"></span></h1>
    <div class="front__person">
      <p class="front__name">Mara Ellison</p>
      <p class="front__role">director</p>
    </div>
    <ul class="front__contacts">
      <li>
        <svg viewBox="0 0 16 16" aria-hidden="true"><path d="M3.5 1.5l2.5 0 1.2 3.2-1.7 1.2c.8 1.8 2.2 3.2 4 4l1.2-1.7 3.2 1.2 0 2.5c0 .8-.7 1.5-1.5 1.5C6.6 13.4 2.6 9.4 2 3c0-.8.7-1.5 1.5-1.5z"/></svg>
        <span>512 555 0142</span>
      </li>
      <li>
        <svg viewBox="0 0 16 16" aria-hidden="true"><path d="M4 1h6l2 2v3H4z M2 7h12v6H2z M5 14h6v1H5z"/></svg>
        <span>512 555 0143</span>
      </li>
      <li>
        <svg viewBox="0 0 16 16" aria-hidden="true"><path d="M1 3h14v10H1z M2 4l6 5 6-5" stroke="#ffffff" stroke-width="1"/></svg>
        <span>info@lumadesk.com.au</span>
      </li>
    </ul>
    <address class="front__address">
      418 Halden Row<br>Corvell TX 78010
    </address>
  </section>

  <section class="card card--back" aria-label="Business card back">
    <div class="back__lockup">
      <p class="back__brand">lumadesk<span class="back__mark" aria-hidden="true"></span></p>
      <p class="back__url">www.lumadesk.com.au</p>
    </div>
  </section>
</main>
</body>
</html>
```